Corvane Paintless Dent Removal

Our company works on vehicles removing dents using a highly skilled trade which the metal is massaged out with special tools without disturbing the original paint, hence paintless dent removal. Besides keeping the paint and metal original its also very environmentally friendly since no paint or toxic fillers are used. Also we we are one of the most experienced companies in the business with 25 years

Target Market(s)

Retail Automobile consumers, Auto Dealerships and Auto Body Shops

Industry/Entity Type

Auto Repair

Contact Information for Business Card

Dale Hollister
PO Box 518 Brookmere, NY 11962
631-555-0148
corvanepdr@mailbox-example.com
website corvanepdr.example
youtube corvane paintless dent removal
25 years of experience removing Dents, Dings and Hail Damage

Font styles to use
Serif
Sans Serif

Colors

Designer to choose colors to be used in the design.

Requirements
Must have
• I do like things that are simple but classy and somewhat bold, also I like my logo so that should be somewhat important

```html
<!DOCTYPE html>
<html lang="en">
<head>
<meta charset="utf-8">
<title>Corvane Paintless Dent Removal – Business Card</title>
<link rel="stylesheet" href="https://fonts.googleapis.com/css2?family=Roboto:wght@400;900&family=Roboto+Condensed:wght@700&display=swap">
<style>
  :root {
    --navy: #13294b;
    --green: #7dc614;
    --paper: #f1f1f1;
    --ink: #444444;
    --rule: #8a8a8a;
    --gold: #c9a233;
    --backdrop: #2a2a2a;
    --white: #ffffff;
  }
  * { margin: 0; padding: 0; box-sizing: border-box; }
  html, body { width: 1200px; height: 960px; overflow: hidden; }
  body {
    position: relative;
    background: var(--backdrop);
    font-family: "Roboto", Arial, sans-serif;
  }
  .card {
    position: absolute;
    width: 600px;
    height: 342px;
    overflow: hidden;
  }
  .card--front { left: 314px; top: 113px; background: var(--paper); }
  .card--back { left: 311px; top: 472px; background: var(--navy); }

  .experience-seal {
    position: absolute;
    left: 31px; top: 35px;
    width: 76px; height: 76px;
    border-radius: 50%;
    background: radial-gradient(circle, #1b1b1b 0 58%, var(--gold) 60% 100%);
  }
  .brand-name {
    position: absolute;
    right: 44px; top: 52px;
    color: var(--navy);
    font-weight: 900;
    text-align: center;
    line-height: 1;
  }
  .brand-name__word { display: block; font-size: 34px; letter-spacing: -0.5px; }
  .brand-name__tag { display: block; font-size: 13px; margin-top: 4px; }

  .holder-name {
    position: absolute;
    left: 32px; top: 196px;
    font-family: "Roboto Condensed", Arial, sans-serif;
    font-weight: 700;
    font-size: 21px;
    color: var(--navy);
    text-transform: uppercase;
  }
  .divider {
    position: absolute;
    left: 34px; top: 228px;
    width: 526px; height: 2px;
    background: var(--rule);
  }
  .contact-list {
    position: absolute;
    left: 32px; top: 241px;
    list-style: none;
    font-size: 14px;
    color: var(--ink);
  }
  .contact-list li { display: flex; align-items: center; height: 19.5px; }
  .contact-list svg { width: 13px; height: 13px; margin-right: 9px; fill: var(--navy); }
  .mailing-address {
    position: absolute;
    right: 39px; top: 262px;
    text-align: right;
    font-size: 14px;
    line-height: 19px;
    color: var(--ink);
    font-style: normal;
  }
  .footer-bands { position: absolute; left: 0; top: 310px; width: 600px; height: 32px; }
  .footer-url {
    position: absolute;
    right: 40px; top: 316px;
    color: var(--white);
    font-size: 14px;
    letter-spacing: 1.6px;
  }

  .back-brand__word,
  .back-brand__tag,
  .back-url {
    position: absolute;
    left: 42px;
    color: var(--white);
    line-height: 1;
    white-space: nowrap;
  }
  .back-brand__word { top: 238px; font-size: 44px; font-weight: 900; letter-spacing: -1px; }
  .back-brand__tag { top: 278px; font-size: 15px; font-weight: 900; }
  .back-url { top: 297px; font-size: 13px; letter-spacing: 2.4px; }
</style>
</head>
<body>
  <section class="card card--front" aria-label="Business card front">
    <div class="experience-seal" aria-hidden="true"></div>
    <div class="brand-name">
      <span class="brand-name__word">CORVANE</span>
      <span class="brand-name__tag">Paintless Dent Removal</span>
    </div>

    <h1 class="holder-name">Dale Hollister</h1>
    <div class="divider"></div>

    <ul class="contact-list">
      <li>
        <svg viewBox="0 0 24 24" aria-hidden="true"><path d="M6.6 10.8a15.1 15.1 0 0 0 6.6 6.6l2.2-2.2a1 1 0 0 1 1-.25 11.4 11.4 0 0 0 3.6.57 1 1 0 0 1 1 1V20a1 1 0 0 1-1 1A17 17 0 0 1 3 4a1 1 0 0 1 1-1h3.5a1 1 0 0 1 1 1c0 1.25.2 2.45.57 3.57a1 1 0 0 1-.25 1z"/></svg>
        631-555-0148
      </li>
      <li>
        <svg viewBox="0 0 24 24" aria-hidden="true"><path d="M2 5h20v14H2zm2 2v.5l8 5 8-5V7zm0 2.8V17h16V9.8l-8 5z"/></svg>
        corvanepdr@mailbox-example.com
      </li>
      <li>
        <svg viewBox="0 0 24 24" aria-hidden="true"><rect x="2" y="5" width="20" height="14" rx="3"/></svg>
        corvane paintless dent removal
      </li>
    </ul>

    <address class="mailing-address">
      PO Box 518<br>Brookmere, NY 11962
    </address>

    <svg class="footer-bands" viewBox="0 0 600 32" aria-hidden="true">
      <polygon points="0,9 342,9 330,22 0,22" fill="var(--green)"/>
      <polygon points="350,0 600,0 600,32 316,32" fill="var(--navy)"/>
      <polygon points="0,22 330,22 318,24 0,24" fill="#c8c8c8"/>
    </svg>
    <div class="footer-url">www.corvanepdr.example</div>
  </section>

  <section class="card card--back" aria-label="Business card back">
    <span class="back-brand__word">CORVANE</span>
    <span class="back-brand__tag">Paintless Dent Removal</span>
    <div class="back-url">www.corvanepdr.example</div>
  </section>
</body>
</html>
```